I need a business card designed using the logo provided either vertical or horizontal......Harbourline Property Group is an Australian based real estate company that caters for the upper end of the market so the design of the business card "must reflect" the companies image!!
Colour combinations are optional but "must be realistic" and must be able to be accurately useable CMYK colours.
Please consider that any colours used "must be able to be used" and be suitable in following designs for "pull out banner signs" and "real estate signs".
The colours and the font in the attached designs are for example and other combinations are encouraged.
Target Market(s)
The High End of the Australian real estate market
Industry/Entity Type
Business
Contact Information for Business Card
Logo - Business Name - Director + Licensed Real Estate Agent - Mobile Number (Cell Phone) - Business Number - Fax - Email Address - Web address
Requirements
Must have
- Designs and colours (CMYK) that can easily be interpreted by an Australian printer.
Nice to have
- Some alternative ideas on colour and font..........the ones provided are ok and have been provided as an example but I am looking for alternative ideas
Should not have
- Loud, overly bright colours. Designs that do not reflect the professional standards of the business.
- Designs that look good on a computer monitor but can not be re-created on a printing press.............this is most important when it comes to shading etc.

```html
<!DOCTYPE html>
<html lang="en">
<head>
<meta charset="utf-8">
<title>Harbourline Property Group – Business Card</title>
<link rel="stylesheet" href="https://fonts.googleapis.com/css2?family=Michroma&family=Open+Sans:wght@400&display=swap">
<style>
  :root {
    --backdrop: #e4e4e4;
    --card: #ffffff;
    --ink: #1f1f1f;
    --ink-soft: #555555;
    --gold: #a87425;
    --sand: #c2b488;
    --shadow: rgba(0, 0, 0, 0.12);
  }
  * { margin: 0; padding: 0; box-sizing: border-box; }
  html, body {
    width: 1200px;
    height: 1192px;
    overflow: hidden;
    background: var(--backdrop);
  }
  .sheet {
    width: 1200px;
    height: 1192px;
    display: flex;
    flex-direction: column;
    align-items: center;
    justify-content: center;
    gap: 64px;
  }
  .card {
    position: relative;
    width: 900px;
    height: 514px;
    background: var(--card);
    box-shadow: 0 6px 24px var(--shadow);
    overflow: hidden;
  }

  /* Brand face */
  .brand-face .wordmark {
    position: absolute;
    left: 120px;
    top: 150px;
    display: flex;
    align-items: center;
    gap: 28px;
  }
  .brand-mark-square {
    width: 64px;
    height: 64px;
    background: var(--gold);
  }
  .wordmark-name {
    font-family: "Michroma", sans-serif;
    font-size: 30px;
    line-height: 1.35;
    letter-spacing: 4px;
    text-transform: uppercase;
    color: var(--ink);
  }
  .brand-rule {
    position: absolute;
    left: 0;
    bottom: 0;
    width: 100%;
    height: 14px;
    background: var(--gold);
  }
  .brand-rule-thin {
    position: absolute;
    left: 0;
    bottom: 22px;
    width: 100%;
    height: 4px;
    background: var(--sand);
  }

  /* Contact face */
  .contact-face .holder {
    position: absolute;
    left: 70px;
    top: 70px;
  }
  .holder-name {
    font-family: "Michroma", sans-serif;
    font-size: 22px;
    letter-spacing: 5px;
    text-transform: uppercase;
    color: var(--ink);
  }
  .holder-role {
    margin-top: 10px;
    font-family: "Michroma", sans-serif;
    font-size: 14px;
    letter-spacing: 2px;
    text-transform: uppercase;
    color: var(--gold);
  }
  .holder-company {
    margin-top: 22px;
    font-family: "Michroma", sans-serif;
    font-size: 14px;
    letter-spacing: 2px;
    text-transform: uppercase;
    color: var(--gold);
  }
  .contact-list {
    list-style: none;
    margin-top: 14px;
    font-family: "Open Sans", sans-serif;
    font-size: 19px;
    color: var(--ink-soft);
  }
  .contact-list li {
    display: flex;
    align-items: center;
    gap: 14px;
    height: 34px;
  }
  .contact-list .plain { padding-left: 34px; }
  .contact-icon {
    width: 20px;
    height: 20px;
    flex: none;
    stroke: var(--gold);
    fill: none;
    stroke-width: 1.8;
  }
  .contact-face .wordmark {
    position: absolute;
    right: 60px;
    bottom: 120px;
    display: flex;
    align-items: center;
    gap: 16px;
  }
  .contact-face .brand-mark-square { width: 36px; height: 36px; }
  .contact-face .wordmark-name { font-size: 17px; letter-spacing: 2px; }
  .contact-face .brand-rule { height: 10px; }
</style>
</head>
<body>
<main class="sheet">

  <section class="card brand-face" aria-label="Card front">
    <div class="wordmark">
      <span class="brand-mark-square"></span>
      <p class="wordmark-name">Harbourline<br>Property Group</p>
    </div>
    <div class="brand-rule-thin"></div>
    <div class="brand-rule"></div>
  </section>

  <section class="card contact-face" aria-label="Card back">
    <div class="holder">
      <p class="holder-name">Daniel Marsh</p>
      <p class="holder-role">CEO</p>
      <p class="holder-company">Harbourline Property Group</p>
      <ul class="contact-list">
        <li class="plain">18 Wharf Lane, Harbour Point, Sydney.</li>
        <li>
          <svg class="contact-icon" viewBox="0 0 20 20" aria-hidden="true"><rect x="5" y="2" width="10" height="16" rx="2"/><line x1="9" y1="15" x2="11" y2="15"/></svg>
          +61 412 555 019
        </li>
        <li>
          <svg class="contact-icon" viewBox="0 0 20 20" aria-hidden="true"><path d="M3 8 Q10 1 17 8 L15 10 L12 8 L12 6 Q10 5 8 6 L8 8 L5 10 Z"/><rect x="4" y="12" width="12" height="5" rx="1"/></svg>
          +61 2 5550 1742
        </li>
        <li>
          <svg class="contact-icon" viewBox="0 0 20 20" aria-hidden="true"><rect x="2" y="4" width="16" height="12"/><polyline points="2,4 10,11 18,4"/></svg>
          daniel@harbourlinegroup.com
        </li>
        <li>
          <svg class="contact-icon" viewBox="0 0 20 20" aria-hidden="true"><circle cx="10" cy="10" r="8"/><ellipse cx="10" cy="10" rx="3.5" ry="8"/><line x1="2" y1="10" x2="18" y2="10"/></svg>
          www.harbourlinegroup.com
        </li>
      </ul>
    </div>
    <div class="wordmark">
      <span class="brand-mark-square"></span>
      <p class="wordmark-name">Harbourline<br>Property Group</p>
    </div>
    <div class="brand-rule"></div>
  </section>

</main>
</body>
</html>
```